ORLA - Óptica Médica - web design and concept

Website concept - Create and develop our website design and structure. ORLA is an optical store chain, and we are looking to establish our web and digital concept. In attachment there are several pictures about our stores and our logo.

The website structure should be user friendly. Colors should be light and the design as simple and minimalist as possible. There are different variations of the logothat can be used, check the file.

The website will include optical collections and sun collections as an online store. Also, a medical menu should be considered in order for clients to schedule optometry appointments. There should also be a menu for client assistance where the clients can read about glass maintenance in our workshop.
Updates

Low design quality

Number of Pages Required

5+ page

Font styles to use
Serif
Sans Serif

Requirements
Must have
• Must be user-friendly and minimalist.
• Please USE PICTURES FROM THE BRANDS we sell: MERUN, BOSKA, PNW, KOLE, BAMPE
Nice to have
• Nice to inspire: ZEK glasses (see website https://ch.shopzek.com/en/)
• Nice to inspire: https://merun-eyewear.com/
• Nice to ispire: https://www.pnwglobe.com/en/
Should not have
• Hysteric colors and shapes

```html
<!DOCTYPE html>
<html lang="en">
<head>
<meta charset="utf-8">
<title>ORLA – Óptica Médica – Web Concept</title>
<link href="https://fonts.googleapis.com/css2?family=Cinzel:wght@600&family=Montserrat:wght@400;500;600&family=Lora:ital,wght@0,400;1,400;1,600&display=swap" rel="stylesheet">
<style>
:root{
  --stage:#3a3a3a;
  --page:#ffffff;
  --ink:#2a2a2a;
  --muted:#6f7a80;
  --hero-deep:#163f49;
  --hero-mid:#2b6774;
  --teal:#2ab0bd;
  --teal-soft:#5fcdc6;
  --line:#e3e8ea;
  --band:#eef2f4;
  --footer:#dde5e8;
}
*{box-sizing:border-box;margin:0;padding:0}
html,body{width:1200px;height:840px;overflow:hidden}
body{background:var(--stage);font-family:"Montserrat",sans-serif;color:var(--ink);position:relative}
.page{position:absolute;top:30px;width:540px;height:780px;background:var(--page);overflow:hidden}
.page--shop{left:40px}
.page--clinic{left:620px}

/* shop page */
.hero{position:relative;height:240px;background:linear-gradient(100deg,var(--hero-deep),var(--hero-mid) 55%,#3d7d88);color:#dff2f4}
.hero__photo{position:absolute;left:0;top:0;width:230px;height:240px;background:radial-gradient(ellipse at 40% 45%,#3f7480,transparent 70%)}
.brand{position:absolute;left:26px;top:16px;display:flex;align-items:center;gap:6px;font-size:13px;letter-spacing:3px;font-weight:500;color:#e8f6f7}
.brand__dot{width:7px;height:7px;border-radius:50%;background:currentColor}
.hero__offer{position:absolute;right:24px;top:62px;text-align:right}
.hero__kicker{font-family:"Cinzel",serif;font-size:11px;letter-spacing:1.5px;color:#9fd6dc}
.hero__title{font-family:"Cinzel",serif;font-size:28px;letter-spacing:2px;color:#9fd6dc;margin-top:4px}
.hero__cta{font-size:6px;letter-spacing:1px;color:#9fd6dc;margin-top:8px;margin-right:80px;border-bottom:1px solid #9fd6dc;display:inline-block}
.hero__note{position:absolute;left:150px;top:128px;width:210px;padding:12px 10px 10px;border:1px solid rgba(255,255,255,.45);background:rgba(255,255,255,.12);text-align:center;font-size:6.5px;line-height:1.55;color:#fff}
.hero__more{display:inline-block;margin-top:8px;padding:3px 14px;border:1px solid rgba(255,255,255,.7);font-size:5px;letter-spacing:.8px}
.hero__scroll{position:absolute;left:50%;bottom:-10px;transform:translateX(-50%);width:22px;height:22px;border-radius:50%;background:var(--hero-deep);display:flex;align-items:center;justify-content:center}
.arrivals__title{font-family:"Cinzel",serif;font-size:15px;letter-spacing:1.5px;text-align:center;margin:26px 0 18px}
.products{display:grid;grid-template-columns:repeat(3,1fr);row-gap:18px;padding:0 28px}
.product{text-align:center}
.product__img{height:74px;margin:0 10px 8px;border-radius:4px}
.product__name{font-size:10px;letter-spacing:1px;color:#555}
.product__price{font-size:10px;letter-spacing:1px;color:#555;margin-top:2px}
.tone-tortoise{background:linear-gradient(90deg,#f6efe9,#b9704a 50%,#f6efe9)}
.tone-black{background:linear-gradient(90deg,#f3f3f3,#5a5a5a 50%,#f3f3f3)}
.tone-peach{background:linear-gradient(90deg,#fbf3ec,#f0c6a2 50%,#fbf3ec)}
.tone-gift{background:linear-gradient(120deg,#2d2d2d,#5da4d6 55%,#f2f2f2)}
.tone-clip{background:linear-gradient(90deg,#f3f3f3,#333 50%,#f3f3f3)}
.tone-cream{background:linear-gradient(90deg,#f7f2ec,#a86643 50%,#f7f2ec)}
.tone-sun-dark{background:linear-gradient(90deg,#f4f4f4,#3a3a45 50%,#f4f4f4)}
.tone-sun-aviator{background:linear-gradient(90deg,#f6f0ea,#7a4a2a 50%,#f6f0ea)}
.tone-sun-brown{background:linear-gradient(90deg,#f7efe8,#9a5a3a 50%,#f7efe8)}
.collection{position:absolute;bottom:22px;width:100%;text-align:center;font-size:10px;letter-spacing:1px;color:#666}

/* clinic page */
.topbar{display:flex;justify-content:space-between;padding:5px 24px;font-size:5px;color:var(--muted);background:var(--band)}
.nav{display:flex;justify-content:space-between;align-items:center;padding:8px 24px;border-bottom:1px solid var(--line)}
.nav .brand{position:static;color:var(--ink);font-size:10px;letter-spacing:2px}
.nav__menu{display:flex;gap:14px;list-style:none;font-size:6px;font-weight:600}
.nav__menu .is-active{color:var(--teal);border-top:2px solid var(--teal);padding-top:4px}
.page-title{background:linear-gradient(var(--band),#fff);text-align:center;font-family:"Lora",serif;font-style:italic;font-size:11px;padding:14px 0;border-bottom:1px solid var(--line)}
.service{display:flex;gap:16px;padding:22px 24px 0}
.side{width:92px;flex:none}
.side__list{list-style:none;font-family:"Lora",serif;font-style:italic;font-size:5.5px;border:1px solid var(--line)}
.side__list li{padding:6px 6px;border-bottom:1px solid var(--line)}
.side__list .is-active{background:var(--band)}
.hours{margin-top:12px;background:var(--teal);color:#fff;font-size:5px;padding:4px 6px}
.hours div{display:flex;justify-content:space-between;padding:3px 0;border-bottom:1px solid rgba(255,255,255,.3)}
.main{flex:1}
.topic{display:flex;gap:10px;margin-bottom:10px}
.topic__text{flex:1}
.topic__title{font-family:"Lora",serif;font-style:italic;font-weight:600;font-size:8px;margin-bottom:4px}
.topic__title--small{font-size:6px}
.topic__body{font-family:"Lora",serif;font-style:italic;font-size:5px;line-height:1.5;color:var(--muted)}
.topic__photo{width:100px;height:48px;background:linear-gradient(120deg,#d6e2e6,#8aa3ad);flex:none}
.faq{font-family:"Lora",serif;font-style:italic;font-size:5px;color:var(--teal);line-height:1.8}
.pricing{display:flex;margin-top:14px}
.pricing__photo{width:150px;height:150px;background:linear-gradient(90deg,#e9ecef,#c7ccd0 40%,#f3f4f5);flex:none}
.pricing__body{flex:1;padding:0 24px 0 10px}
.pricing__title{font-family:"Lora",serif;font-style:italic;font-size:8px;margin:-22px 0 12px}
.price-table{display:grid;grid-template-columns:1fr 1fr;column-gap:12px}
.price-row{display:flex;justify-content:space-between;font-family:"Lora",serif;font-style:italic;font-size:4.8px;color:var(--teal);padding:5px 0;border-bottom:1px solid var(--line)}
.price-row small{display:block;color:var(--muted);font-size:4.2px;margin-top:2px}
.offer{margin:14px 0 0;background:var(--band);text-align:center;padding:14px 0 12px;font-family:"Lora",serif;font-size:7px}
.btn{display:inline-block;margin-top:8px;background:var(--teal-soft);color:#fff;font-size:4.5px;padding:4px 12px;font-family:"Montserrat",sans-serif}
.footer{position:absolute;left:0;right:0;bottom:0;height:170px;background:var(--footer);border-top:1px solid #cdd8dc}
.footer__grid{display:flex;gap:20px;padding:20px 24px}
.footer__about{width:110px;font-family:"Lora",serif;font-style:italic;font-size:5px;color:var(--muted);line-height:1.5}
.footer__about .brand{position:static;color:var(--ink);font-size:10px;letter-spacing:2px;margin-bottom:8px}
.footer__col h4{font-family:"Lora",serif;font-style:italic;font-size:6px;color:var(--teal);margin-bottom:6px}
.footer__col ul{list-style:none;font-family:"Lora",serif;font-style:italic;font-size:4.5px;line-height:2;color:var(--muted)}
.contact{margin-left:auto;width:120px;background:var(--teal-soft);color:#fff;padding:12px 10px;font-size:5px;line-height:2.2}
.contact__phone{font-size:7px;font-weight:600}
.contact svg{vertical-align:middle;margin-right:4px}
.footer__bar{position:absolute;bottom:0;left:0;right:0;height:20px;background:#f5f7f8;border-top:3px solid var(--teal)}
</style>
</head>
<body>

<section class="page page--shop">
  <header class="hero">
    <div class="hero__photo" role="img" aria-label="Campaign portrait of a model wearing dark optical frames, teal toned"></div>
    <div class="brand"><span class="brand__dot"></span>ORLA</div>
    <div class="hero__offer">
      <p class="hero__kicker">UP TO 60% OFF</p>
      <h1 class="hero__title">SUMMER SALE</h1>
      <span class="hero__cta">SHOP NOW</span>
    </div>
    <div class="hero__note">
      Maître Óptica Médica a prêté serment il y a 6 ans.<br>
      Cet avocat exerce au barreau de Paris.<br>
      Son cabinet est situé au 14 Rue des Tilleuls à ROMA.
      <br><span class="hero__more">READ MORE</span>
    </div>
    <div class="hero__scroll">
      <svg width="8" height="12" viewBox="0 0 8 12"><rect x="1" y="1" width="6" height="10" rx="3" fill="none" stroke="#cfe9ec" stroke-width="1"/><line x1="4" y1="3" x2="4" y2="5" stroke="#cfe9ec"/></svg>
    </div>
  </header>

  <h2 class="arrivals__title">NEW ARRIVALS</h2>
  <div class="products">
    <article class="product"><div class="product__img tone-tortoise" role="img" aria-label="Tortoiseshell optical frame"></div><p class="product__name">KELDA</p><p class="product__price">€400.00</p></article>
    <article class="product"><div class="product__img tone-black" role="img" aria-label="Black and grey optical frame"></div><p class="product__name">KELDA</p><p class="product__price">€400.00</p></article>
    <article class="product"><div class="product__img tone-peach" role="img" aria-label="Peach translucent optical frame"></div><p class="product__name">KELDA</p><p class="product__price">€400.00</p></article>
    <article class="product"><div class="product__img tone-gift" role="img" aria-label="Gift voucher box with frame and blue cloth"></div><p class="product__name">VOUCHER</p><p class="product__price">€100.00</p></article>
    <article class="product"><div class="product__img tone-clip" role="img" aria-label="Black frame with flip-up sun clip"></div><p class="product__name">KELDA</p><p class="product__price">€400.00</p></article>
    <article class="product"><div class="product__img tone-cream" role="img" aria-label="Two-tone tortoise and cream frame"></div><p class="product__name">KELDA</p><p class="product__price">€400.00</p></article>
    <article class="product"><div class="product__img tone-sun-dark" role="img" aria-label="Black square sunglasses"></div></article>
    <article class="product"><div class="product__img tone-sun-aviator" role="img" aria-label="Tortoise aviator sunglasses"></div></article>
    <article class="product"><div class="product__img tone-sun-brown" role="img" aria-label="Round brown sunglasses"></div></article>
  </div>
  <p class="collection">HARBOUR - SAIL CLUB COLLECTION</p>
</section>

<section class="page page--clinic">
  <div class="topbar"><span>An eye care clinic for the whole family</span><span>Address: 14 Harlow Street, Lindale</span></div>
  <nav class="nav">
    <div class="brand"><span class="brand__dot"></span>ORLA</div>
    <ul class="nav__menu"><li>Home</li><li class="is-active">Departments</li><li>Our Doctors</li><li>News</li><li>Contact Us</li></ul>
  </nav>
  <h1 class="page-title">Óptica Médica</h1>

  <div class="service">
    <aside class="side">
      <ul class="side__list">
        <li>Surgery and Radiology</li><li>Family Medicine</li><li>Women's Health</li>
        <li class="is-active">Opticians</li><li>Pediatrics</li><li>Dermatology</li>
      </ul>
      <div class="hours">
        <div><span>Mon – Fri</span><span>8:00 – 18:00</span></div>
        <div><span>Sat – Sun</span><span>8:00 – 14:00</span></div>
        <div><span>Field Week</span><span>10:00 – 16:00</span></div>
        <div><span>All holidays</span><span>Closed</span></div>
      </div>
    </aside>
    <div class="main">
      <div class="topic">
        <div class="topic__text">
          <h3 class="topic__title">Sight Checking</h3>
          <p class="topic__body">Most people check their eyes too rarely. A short exam helps find early changes, keeps vision sharp and lets us choose the right lenses for daily life.</p>
        </div>
        <div class="topic__photo" role="img" aria-label="Optician with a client in the store"></div>
      </div>
      <div class="topic">
        <div class="topic__text">
          <h3 class="topic__title topic__title--small">Our Laboratory</h3>
          <p class="topic__body">Our workshop cuts and fits every lens in house, so frames are ready faster and adjusted to your face.</p>
          <p class="faq">How often should I have my eyes tested?<br>How old does my child have to be before test?</p>
        </div>
        <div class="topic__photo" role="img" aria-label="Optometrist examining a patient with a slit lamp"></div>
      </div>
    </div>
  </div>

  <div class="pricing">
    <div class="pricing__photo" role="img" aria-label="Frame resting on a lens measurement sketch"></div>
    <div class="pricing__body">
      <h3 class="pricing__title">Pricing Table</h3>
      <div class="price-table">
        <div class="price-row"><span>Simple Medical Form<small>Glasses can be quite pricey, even excluding the cost of frames.</small></span><span>$100</span></div>
        <div class="price-row"><span>Cost of contacts<small>Glasses can be quite pricey, even excluding the cost of frames.</small></span><span>$30</span></div>
        <div class="price-row"><span>Digital Retinal Photograph</span><span>$70</span></div>
        <div class="price-row"><span>Additional Services</span><span>$30</span></div>
        <div class="price-row"><span>Simple Aviation Form</span><span>$105</span></div>
        <div class="price-row"><span>Low Vision Aid Assessment</span><span>$22</span></div>
        <div class="price-row"><span>Emergency Appointment</span><span>$100</span></div>
        <div class="price-row"><span>DVLA Acuity Test</span><span>$20</span></div>
      </div>
      <div class="offer">Get 10% Off on All Prescription Glasses<br><span class="btn">Make an Appointment</span></div>
    </div>
  </div>

  <footer class="footer">
    <div class="footer__grid">
      <div class="footer__about">
        <div class="brand"><span class="brand__dot"></span>ORLA</div>
        <p>Caring for your eyes should feel simple. Our team is here with calm, clear advice.</p>
        <span class="btn">Buy Vouchers</span>
      </div>
      <div class="footer__col"><h4>Departments</h4><ul><li>Surgery and Radiology</li><li>Family Medicine</li><li>Women's Health</li><li>Optician</li><li>Pediatrics</li><li>Dermatology</li></ul></div>
      <div class="footer__col"><h4>Menu</h4><ul><li>Departments</li><li>Our Doctors</li><li>News</li><li>Shop</li><li>Contact Us</li><li>Book an Appointment</li></ul></div>
      <div class="contact">
        <div><svg width="8" height="8" viewBox="0 0 10 10"><path d="M2 1l2 2-1 1.5c.6 1.2 1.3 1.9 2.5 2.5L7 6l2 2-1.5 1.5C4.5 9 1 5.5.5 2.5z" fill="#fff"/></svg>Emergency number</div>
        <div class="contact__phone">202-555-0187</div>
        <div><svg width="7" height="6" viewBox="0 0 7 6"><rect x=".5" y=".5" width="6" height="5" fill="none" stroke="#fff"/><path d="M.5.5l3 3 3-3" fill="none" stroke="#fff"/></svg>info@orlaoptica.com</div>
        <div><svg width="7" height="6" viewBox="0 0 7 6"><rect x=".5" y=".5" width="6" height="5" fill="none" stroke="#fff"/><path d="M.5.5l3 3 3-3" fill="none" stroke="#fff"/></svg>care@orlaoptica.com</div>
        <div><svg width="6" height="8" viewBox="0 0 6 8"><path d="M3 0a3 3 0 013 3c0 2-3 5-3 5S0 5 0 3a3 3 0 013-3z" fill="#fff"/></svg>14 Harlow Street, Lindale</div>
      </div>
    </div>
    <div class="footer__bar"></div>
  </footer>
</section>

</body>
</html>
```